Business Card Design: recruitment/consultancy for business Thrive360onward

We need a business card design for a new company based in Adelaide Australia called Thrive360onward. Our Business aims to support people over 50 who may be looking for a career change, have been made redundant or generally looking for employment. We will also be working with businesses to provide them with recruiting solutions, job design, recruitment strategies and customised training. we will also be working with volunteering opportunities for those over 50.
We would like to see the E in thrive360onward strong and dominant. The final design should reflect change for the better, better opportunities, today is the day, make way for the new, all aimed at the 50 plus age group.
Colours we are thinking off include green (money, growth) black and white.... we like the idea of black and white photography with a one dominant colour...think of a of a black and white photo of a woman with dominant red lips...that sort of look

Business

Contact Information for Business Card

Kim, Mavis & Gwen
phone: 0439615028
Thrive360onward@mailbox-example.net
Facebook/Thrive360onward
www.thrive360onward-example.com.au

```html
<!DOCTYPE html>
<html lang="en">
<head>
<meta charset="utf-8">
<title>Thrive360onward business card</title>
<link rel="stylesheet" href="https://fonts.googleapis.com/css2?family=Arimo:wght@400&family=Great+Vibes&display=swap">
<style>
  :root {
    --page-bg: #e9e7e4;
    --card-light: #b9b9b9;
    --card-mid: #9a9a9a;
    --card-dark: #6f6f6f;
    --ink-dark: #3a3a3a;
    --ink-white: #ffffff;
    --ink-soft: #ececec;
    --accent-red: #e0303c;
    --photo-light: #d6d6d6;
    --photo-dark: #1e1e1e;
  }
  * { box-sizing: border-box; margin: 0; padding: 0; }
  html, body { width: 1200px; height: 858px; overflow: hidden; }
  body {
    background: var(--page-bg);
    display: flex;
    align-items: center;
    justify-content: center;
    gap: 56px;
  }
  .card {
    width: 540px;
    height: 309px;
    position: relative;
    overflow: hidden;
    border-radius: 3px;
    box-shadow: 0 10px 28px rgba(0,0,0,0.22);
  }
  .card-front {
    background: linear-gradient(160deg, var(--card-light) 0%, var(--card-mid) 55%, var(--card-dark) 100%);
  }
  .portrait-area {
    position: absolute;
    top: 0; right: 0;
    width: 300px; height: 100%;
    background: radial-gradient(ellipse at 45% 40%, var(--photo-light) 0%, #8c8c8c 45%, var(--photo-dark) 100%);
  }
  .brand {
    position: absolute;
    left: 34px;
    bottom: 92px;
    display: flex;
    align-items: center;
    gap: 10px;
  }
  .brand-dot {
    width: 14px; height: 14px;
    border-radius: 50%;
    background: var(--accent-red);
  }
  .brand-name {
    font-family: "Arimo", Arial, sans-serif;
    font-size: 30px;
    color: var(--ink-dark);
    letter-spacing: 0.5px;
  }
  .front-url {
    position: absolute;
    left: 58px;
    bottom: 62px;
    font-family: "Arimo", Arial, sans-serif;
    font-size: 13px;
    color: var(--ink-dark);
  }
  .card-back {
    background: linear-gradient(150deg, var(--card-light) 0%, var(--card-mid) 50%, var(--card-dark) 100%);
    display: flex;
    flex-direction: column;
    justify-content: center;
    padding-left: 70px;
  }
  .names {
    font-family: "Great Vibes", cursive;
    font-size: 40px;
    color: var(--ink-white);
    margin-bottom: 14px;
    line-height: 1.1;
  }
  .contact-list { list-style: none; }
  .contact-list li {
    font-family: "Great Vibes", cursive;
    font-size: 22px;
    color: var(--ink-soft);
    line-height: 1.25;
  }
</style>
</head>
<body>
  <section class="card card-front">
    <div class="portrait-area" role="img" aria-label="Black and white portrait photograph of a woman in a hat with bold red lips"></div>
    <div class="brand">
      <span class="brand-dot"></span>
      <span class="brand-name">thrive360onward</span>
    </div>
    <p class="front-url">www.thrive360onward-example.com.au</p>
  </section>

  <section class="card card-back">
    <h1 class="names">Kim, Mavis &amp; Gwen</h1>
    <ul class="contact-list">
      <li>0439615028</li>
      <li>Thrive360onward@mailbox-example.net</li>
      <li>Facebook/Thrive360onward</li>
      <li>www.thrive360onward-example.com.au</li>
    </ul>
  </section>
</body>
</html>
```